QAMBRO THERAPEUTICS

physical therapy company. need a flashy image and named logo, website link, that I can also use on Letterhead and business cards. Clean, sharp, modern, eye catching. 3 colors? Some shine. Needs to stand out and not be trendy or too much cursive . Androgynous image of a human body is ok. A spine included is ok. Prefer lines to curves for font types. Warm colors but strong impact. Will need to have some contact info and border mission statement on it.
Updates

Target Market(s)

Target market is large corporations, wealthy individuals, medical doctors

Industry/Entity Type

Medical, physical therapy

Contact Information for Business Card

Name, Owner, phone, email, and website

Colors
0054AA
0677BA
7BADD7
CADEEF
E8F1F8

Requirements
Must have
• See above- something about BALANCE, wellness, strength etc
Nice to have
• Contrast, depth
Should not have
• No cursive

```html
<!DOCTYPE html>
<html lang="en">
<head>
<meta charset="utf-8">
<title>Qambro Therapeutics — Business Card</title>
<link rel="stylesheet" href="https://fonts.googleapis.com/css2?family=Poppins:wght@400;500;700&display=swap">
<style>
  :root{
    --brand-blue:#0054aa;
    --brand-blue-bright:#0a5fc4;
    --mid-blue:#0677ba;
    --sky:#7badd7;
    --ice:#cadeef;
    --mist:#e8f1f8;
    --white:#ffffff;
    --backdrop:#1c1c1e;
  }
  *{box-sizing:border-box;margin:0;padding:0}
  html,body{width:1200px;height:1015px;overflow:hidden}
  body{
    background:radial-gradient(ellipse at center,#3a3a3c 0%,var(--backdrop) 75%);
    font-family:"Poppins",sans-serif;
    position:relative;
  }
  .card{
    position:absolute;
    width:760px;height:434px;
    border-radius:4px;
    overflow:hidden;
    box-shadow:0 18px 40px rgba(0,0,0,.55);
  }
  /* Front */
  .card--front{left:70px;top:50px;background:var(--brand-blue-bright)}
  .front-artwork{
    position:absolute;inset:0;
    background:
      radial-gradient(ellipse 38% 60% at 55% 45%, rgba(123,173,215,.55) 0%, rgba(6,119,186,.25) 55%, transparent 80%),
      linear-gradient(135deg,var(--brand-blue) 0%,var(--brand-blue-bright) 55%,var(--brand-blue) 100%);
  }
  .front-logo{
    position:absolute;left:0;right:0;top:150px;
    text-align:center;color:var(--white);font-weight:700;
  }
  .front-logo .logo-word{display:block;font-size:76px;line-height:1;letter-spacing:2px}
  .front-logo .logo-sub{display:block;font-size:27px;letter-spacing:3px;margin-top:6px}
  /* Back */
  .card--back{left:370px;top:531px;background:var(--brand-blue)}
  .back-shapes{position:absolute;inset:0}
  .back-logo{
    position:absolute;left:430px;top:112px;width:320px;
    text-align:center;color:var(--brand-blue);font-weight:700;
  }
  .back-logo .logo-word{display:block;font-size:64px;line-height:1;letter-spacing:1px}
  .back-logo .logo-sub{display:block;font-size:23px;letter-spacing:2px;margin-top:4px}
  .holder{position:absolute;left:56px;top:120px;color:var(--white)}
  .holder-name{font-size:25px;font-weight:700;letter-spacing:1px}
  .holder-role{font-size:17px;font-weight:400;margin-top:2px}
  .contact-list{position:absolute;left:56px;top:300px;list-style:none;color:var(--white)}
  .contact-list li{display:flex;align-items:center;gap:10px;font-size:17px;line-height:1.55}
  .contact-list svg{width:17px;height:17px;flex:none}
</style>
</head>
<body>

<section class="card card--front">
  <div class="front-artwork" role="img" aria-label="Blue anatomical human figure with outstretched arms over a soft blue spine background"></div>
  <div class="front-logo">
    <span class="logo-word">QAMBRO</span>
    <span class="logo-sub">THERAPEUTICS</span>
  </div>
</section>

<section class="card card--back">
  <svg class="back-shapes" viewBox="0 0 760 434" aria-hidden="true">
    <rect width="760" height="434" fill="var(--brand-blue)"/>
    <circle cx="588" cy="170" r="268" fill="var(--sky)"/>
    <circle cx="602" cy="160" r="264" fill="var(--white)"/>
  </svg>
  <div class="back-logo">
    <span class="logo-word">QAMBRO</span>
    <span class="logo-sub">THERAPEUTICS</span>
  </div>
  <div class="holder">
    <p class="holder-name">MARCUS ELLERY</p>
    <p class="holder-role">Managing Director</p>
  </div>
  <ul class="contact-list">
    <li>
      <svg viewBox="0 0 24 24" fill="none" stroke="currentColor" stroke-width="2.2" stroke-linecap="round" stroke-linejoin="round"><path d="M22 16.9v3a2 2 0 0 1-2.2 2 19.8 19.8 0 0 1-8.6-3.1 19.5 19.5 0 0 1-6-6A19.8 19.8 0 0 1 2.1 4.2 2 2 0 0 1 4.1 2h3a2 2 0 0 1 2 1.7c.1 1 .4 1.9.7 2.8a2 2 0 0 1-.5 2.1L8 9.9a16 16 0 0 0 6 6l1.3-1.3a2 2 0 0 1 2.1-.4c.9.3 1.8.6 2.8.7a2 2 0 0 1 1.7 2z"/></svg>
      044-555 018 274
    </li>
    <li>
      <svg viewBox="0 0 24 24" fill="none" stroke="currentColor" stroke-width="2.2" stroke-linejoin="round"><rect x="2" y="5" width="20" height="14" rx="1"/><path d="M2 6l10 7 10-7"/></svg>
      hello@qambroclinic.com
    </li>
    <li>
      <svg viewBox="0 0 24 24" fill="none" stroke="currentColor" stroke-width="2"><circle cx="12" cy="12" r="10"/><path d="M2 12h20M12 2c3 3 3 17 0 20M12 2c-3 3-3 17 0 20"/></svg>
      www.qambroclinic.com
    </li>
  </ul>
</section>

</body>
</html>
```